Waste management company seeks a new website design

We need a website design for an environmental services company called 'Laanemetsa Haldusgrupp.' We manage waste collection and recycling for 100K+ households and businesses across Estonia. Please use logos and colors from attached CVI file. The design should be extensively usable for our self-service portal and have a mobile-first approach as it will be turned into an app in the future. The new website should highlight our commitment to sustainability and provide easy access to our services with a clean, modern design. UX inspiration from https://ruvako.eu/et-ee/

```html
<!DOCTYPE html>
<html lang="en">
<head>
<meta charset="utf-8">
<title>Laanemetsa Haldusgrupp – Waste Collection &amp; Recycling</title>
<link href="https://fonts.googleapis.com/css2?family=Poppins:wght@300;400;500&display=swap" rel="stylesheet">
<style>
:root{
  --lime:#c8d42b;
  --lime-dark:#b5c11f;
  --ink:#1f1f1f;
  --text:#444;
  --muted:#6f6f6f;
  --brand-grey:#8b807a;
  --card:#f4f2f1;
  --line:#d9d9d9;
  --white:#fff;
}
*{box-sizing:border-box;margin:0;padding:0}
html,body{width:1200px;height:4831px;overflow:hidden}
body{position:relative;background:var(--white);font-family:"Poppins",sans-serif;color:var(--ink)}
.abs{position:absolute}
.lime-rule{position:absolute;height:4px;width:44px;background:var(--lime)}
.btn{position:absolute;display:flex;align-items:center;justify-content:center;border-radius:26px;background:var(--lime);color:var(--ink);font-size:18px;font-weight:400}
.photo{position:absolute;border-radius:10px}

/* header */
.site-header{position:absolute;left:0;top:0;width:1200px;height:129px}
.brand{position:absolute;display:flex;align-items:center;gap:14px}
.brand-dot{width:56px;height:56px;border-radius:50%;background:var(--lime)}
.brand-name{font-size:24px;line-height:27px;font-weight:500;color:var(--brand-grey)}
.contact-bar{position:absolute;left:600px;top:30px;display:flex;gap:26px;font-size:15px;color:var(--ink)}
.contact-bar span{display:flex;align-items:center;gap:8px}
.main-nav{position:absolute;left:529px;top:70px;display:flex;gap:26px;font-size:16px;align-items:center}
.main-nav a{color:var(--ink);text-decoration:none}
.main-nav .active{background:var(--lime);border-radius:16px;padding:3px 12px}

/* hero */
.hero{position:absolute;left:0;top:129px;width:1200px;height:507px;
  background:linear-gradient(100deg,#c98a55 0%,#9a6a44 30%,#5f5a34 55%,#37402a 75%,#5a4a2e 100%)}
.hero h1{position:absolute;left:649px;top:78px;width:420px;font-size:40px;line-height:46px;font-weight:300;color:var(--ink)}
.hero-dots{position:absolute;left:558px;top:451px;display:flex;gap:11px}
.hero-dots i{width:12px;height:12px;border-radius:50%;background:#fff;display:block}
.hero-dots i.on{background:var(--lime);border:2px solid #fff}

/* headings */
.section-title{position:absolute;left:0;width:1200px;text-align:center;font-size:30px;font-weight:300;color:var(--ink)}
.section-title.sub{color:var(--brand-grey);font-weight:400}
.h-left{position:absolute;font-size:30px;font-weight:300;line-height:48px;color:var(--ink)}

/* welcome features */
.intro{position:absolute;left:634px;top:920px;width:425px;font-size:13.5px;line-height:22px;color:var(--text)}
.feature{position:absolute;left:634px;width:440px;display:flex;gap:24px}
.feature-icon{flex:none;width:68px;height:68px;border-radius:50%;background:var(--lime);display:flex;align-items:center;justify-content:center}
.feature h3{font-size:15px;font-weight:400;margin-top:2px;margin-bottom:6px}
.feature p{font-size:12px;line-height:17px;color:var(--text)}

/* services */
.services-lead{position:absolute;left:0;top:1524px;width:1200px;text-align:center;font-size:14px;color:var(--text)}
.service-card{position:absolute;width:304px;height:252px;border-radius:10px;background:var(--card)}
.service-card.featured{background:var(--lime)}
.service-card h3{position:absolute;left:33px;top:30px;font-size:21px;font-weight:400;line-height:28px}
.service-card p{position:absolute;left:33px;top:110px;width:170px;font-size:11.5px;line-height:17px;color:var(--text)}
.service-card .mini-btn{position:absolute;left:33px;top:190px;width:86px;height:30px;border-radius:15px;background:var(--lime);font-size:12px;display:flex;align-items:center;justify-content:center}
.service-card.featured .mini-btn{background:#fff}
.service-card .illus{position:absolute;right:22px;top:156px;width:76px;height:76px;border-radius:8px;background:#e3e0dd}
.service-card.featured .illus{background:#b3bf1f}

/* body copy */
.copy{position:absolute;font-size:14px;line-height:21px;color:var(--text);text-align:justify}
.copy p+p{margin-top:16px}

/* stats */
.stat{position:absolute;display:flex;gap:14px;align-items:flex-start}
.stat-icon{width:34px;height:34px;border-radius:50%;background:#e6e3e1;flex:none;margin-top:8px}
.stat b{display:block;font-size:24px;font-weight:400;line-height:30px}
.stat span{display:block;font-size:13px;line-height:16px;color:var(--text)}

/* quote */
.quote{position:absolute;left:131px;top:3373px;width:938px;height:461px;border-radius:12px;background:var(--lime);overflow:hidden}
.quote h2{position:absolute;left:64px;top:62px;font-size:32px;font-weight:300}
.quote .rule{position:absolute;left:64px;top:124px;width:60px;height:2px;background:var(--ink)}
.quote p{position:absolute;left:64px;top:168px;width:285px;font-size:20px;line-height:28px}
.quote .btn{left:64px;top:343px;width:156px;height:49px;background:#fff}
.quote .truck{position:absolute;left:385px;top:0;width:553px;height:461px;background:linear-gradient(120deg,#7fce3a 0%,#5fb32b 55%,#3c6b22 100%)}

/* blog */
.post{position:absolute;width:286px}
.post .thumb{width:286px;height:201px;border-radius:8px}
.post time{display:block;margin-top:22px;font-size:12px;color:var(--text)}
.post h3{margin-top:10px;font-size:18px;font-weight:400;line-height:25px}
.post p{margin-top:10px;font-size:11.5px;line-height:17px;color:var(--text)}

/* footer */
.footer-rule{position:absolute;left:0;top:4451px;width:1200px;height:2px;background:var(--line)}
.footer-col{position:absolute;top:4508px}
.footer-col h4{font-size:15px;font-weight:400;margin-bottom:20px}
.footer-col li{list-style:none;font-size:13px;line-height:24px;color:var(--text)}
.socials{position:absolute;left:215px;top:4636px;display:flex;gap:8px}
.socials i{display:block;width:28px;height:28px;border-radius:50%;background:var(--brand-grey)}
.copyright{position:absolute;left:0;top:4772px;width:1200px;text-align:center;font-size:13px;color:var(--text)}
</style>
</head>
<body>

<header class="site-header">
  <div class="brand" style="left:131px;top:34px">
    <div class="brand-dot"></div>
    <div class="brand-name">Laanemetsa<br>Haldusgrupp</div>
  </div>
  <div class="contact-bar">
    <span><svg width="18" height="14" viewBox="0 0 18 14"><rect x="1" y="1" width="16" height="12" fill="none" stroke="#222" stroke-width="1.4"/><path d="M1 1l8 7 8-7" fill="none" stroke="#222" stroke-width="1.4"/></svg>info@laanemetsahaldus.ee</span>
    <span><svg width="18" height="18" viewBox="0 0 24 24"><path d="M6.6 10.8a15 15 0 006.6 6.6l2.2-2.2a1 1 0 011-.25 11.4 11.4 0 003.6.6 1 1 0 011 1V20a1 1 0 01-1 1A17 17 0 013 4a1 1 0 011-1h3.5a1 1 0 011 1c0 1.25.2 2.45.6 3.6a1 1 0 01-.25 1z" fill="none" stroke="#222" stroke-width="1.5"/></svg>+1 888 888 8888</span>
  </div>
  <nav class="main-nav">
    <a class="active" href="#">Home</a><a href="#">About Us</a><a href="#">Services</a><a href="#">Free Bins</a><a href="#">Support</a><a href="#">Contact us</a>
  </nav>
</header>

<section class="hero" role="img" aria-label="Photo of a woman in a knitted hat breathing fresh air in a sunlit forest">
  <h1>Waste collection and recycling for 100K+ households and businesses across</h1>
  <a class="btn" style="left:651px;top:295px;width:157px;height:52px">Read More</a>
  <div class="hero-dots"><i class="on"></i><i></i><i></i><i></i></div>
</section>

<section class="welcome">
  <div class="abs" style="left:580px;top:694px;width:38px;height:38px;border-radius:50%;background:var(--lime)"></div>
  <h2 class="section-title" style="top:754px">WELCOME TO</h2>
  <h2 class="section-title sub" style="top:801px">LAANEMETSA HALDUSGRUPP</h2>
  <div class="lime-rule" style="left:578px;top:870px"></div>
  <div class="photo" style="left:131px;top:924px;width:463px;height:473px;background:linear-gradient(135deg,#2c4f9a,#6d7fa8 45%,#c9c8c0 70%,#3b5fa8)" role="img" aria-label="Photo of two engineers in hard hats and high-visibility vests at a recycling conveyor"></div>
  <p class="intro">Lorem ipsum dolor sit amet, consectetur adipiscing elit, sed do eiusmod tempor incididunt ut labore et dolore magna aliqua. Ut enim ad minim veniam, quis nostrud exercitation ullamco</p>

  <div class="feature" style="top:1018px">
    <div class="feature-icon"><svg width="34" height="34" viewBox="0 0 24 24"><path d="M6.6 10.8a15 15 0 006.6 6.6l2.2-2.2a1 1 0 011-.25 11.4 11.4 0 003.6.6 1 1 0 011 1V20a1 1 0 01-1 1A17 17 0 013 4a1 1 0 011-1h3.5a1 1 0 011 1c0 1.25.2 2.45.6 3.6a1 1 0 01-.25 1z" fill="none" stroke="#222" stroke-width="1.5"/></svg></div>
    <div><h3>24/7 SERVICE</h3><p>Lorem ipsum dolor sit amet, consectetur adipiscing elit, sed do eiusmod tempor incididunt ut labore</p></div>
  </div>
  <div class="feature" style="top:1118px">
    <div class="feature-icon"><svg width="34" height="34" viewBox="0 0 24 24"><path d="M5 7h14M9 7V4h6v3M7 7l1 13h8l1-13" fill="none" stroke="#222" stroke-width="1.5"/></svg></div>
    <div><h3>ECO-FRIENDLY BINS</h3><p>Lorem ipsum dolor sit amet, consectetur adipiscing elit, sed do eiusmod tempor incididunt ut labore</p></div>
  </div>
  <div class="feature" style="top:1225px">
    <div class="feature-icon"><svg width="34" height="34" viewBox="0 0 24 24"><circle cx="13" cy="7" r="4" fill="none" stroke="#222" stroke-width="1.5"/><path d="M3 15h4l5 3 7-4M3 20h5" fill="none" stroke="#222" stroke-width="1.5"/></svg></div>
    <div><h3>EASY AND AFFORDABLE</h3><p>Lorem ipsum dolor sit amet, consectetur adipiscing elit, sed do eiusmod tempor incididunt ut labore</p></div>
  </div>
  <div class="feature" style="top:1328px">
    <div class="feature-icon"><svg width="34" height="34" viewBox="0 0 24 24"><path d="M12 4a6 6 0 00-3.5 10.9V17h7v-2.1A6 6 0 0012 4zM9.5 20h5" fill="none" stroke="#222" stroke-width="1.5"/></svg></div>
    <div><h3>INDIVIDUALISED SOLUTIONS</h3><p>Lorem ipsum dolor sit amet, consectetur adipiscing elit, sed do eiusmod tempor incididunt ut labore</p></div>
  </div>
</section>

<section class="services">
  <h2 class="section-title" style="top:1470px">OUR SERVICES IN ESTONIA</h2>
  <p class="services-lead">Lorem ipsum dolor sit amet, consectetur adipiscing elit, sed do eiusmod tempor incididunt ut labore</p>
  <div class="lime-rule" style="left:578px;top:1583px"></div>

  <article class="service-card" style="left:131px;top:1644px"><h3>Waste<br>Management</h3><p>Lorem ipsum dolor sit amet, consectetur adipiscing elit, sed do eiusmod tempor incididunt ut labore</p><span class="mini-btn">Read More</span><div class="illus" role="img" aria-label="Line icon of a robotic sorting arm"></div></article>
  <article class="service-card featured" style="left:450px;top:1644px"><h3>Waste<br>Collections</h3><p>Lorem ipsum dolor sit amet, consectetur adipiscing elit, sed do eiusmod tempor incididunt ut labore</p><span class="mini-btn">Read More</span><div class="illus" role="img" aria-label="Line icon of a recycling truck"></div></article>
  <article class="service-card" style="left:767px;top:1644px"><h3>Waste<br>Disposal</h3><p>Lorem ipsum dolor sit amet, consectetur adipiscing elit, sed do eiusmod tempor incididunt ut labore</p><span class="mini-btn">Read More</span><div class="illus" role="img" aria-label="Line icon of a bin and rubbish bag"></div></article>

  <article class="service-card" style="left:131px;top:1914px"><h3 style="top:44px">Recycling</h3><p>Lorem ipsum dolor sit amet, consectetur adipiscing elit, sed do eiusmod tempor incididunt ut labore</p><span class="mini-btn">Read More</span><div class="illus" role="img" aria-label="Line icon of recycling arrows"></div></article>
  <article class="service-card" style="left:450px;top:1914px"><h3>100K+<br>Households</h3><p>Lorem ipsum dolor sit amet, consectetur adipiscing elit, sed do eiusmod tempor incididunt ut labore</p><span class="mini-btn">Read More</span><div class="illus" role="img" aria-label="Line icon of household furniture"></div></article>
  <article class="service-card" style="left:767px;top:1914px"><h3>Free<br>Quote</h3><p>Lorem ipsum dolor sit amet, consectetur adipiscing elit, sed do eiusmod tempor incididunt ut labore</p><span class="mini-btn">Read More</span><div class="illus" role="img" aria-label="Line icon of a quote form and pen"></div></article>
</section>

<section class="why">
  <h2 class="h-left" style="left:135px;top:2245px">WHY RECYCLE?</h2>
  <div class="lime-rule" style="left:135px;top:2311px;width:62px"></div>
  <div class="copy" style="left:135px;top:2355px;width:407px">
    <p>Sed ut perspiciatis unde omnis iste natus error sit volu ptatem accusantium doloremque laudantium, totam rem aperiam, eaque ipsa quae ab illo inventore veritatis et quasi architecto beatae vitae dicta sunt explicabo.</p>
    <p>Nemo enim ipsam voluptatem quia voluptas sit aspernatur aut odit aut fugit, sed quia consequuntur magni dolores eos qui ratione voluptatem sequi nesciunt. Neque porro quisquam est, qui dolorem ipsum quia dolor</p>
    <p>Ut enim ad minima veniam, quis nostrum exercitationem ullam corporis suscipit laboriosam, nisi ut aliquid ex ea com modi consequatur? Quis autem vel eum iure reprehenderit qui in ea voluptate velit esse quam nihil molestiae consequatur, vel illum qui dolorem eum fugiat</p>
  </div>
  <a class="btn" style="left:137px;top:2689px;width:135px;height:47px">Read More</a>
  <div class="photo" style="left:604px;top:2257px;width:465px;height:499px;background:linear-gradient(160deg,#b8752f,#6e4a28 45%,#c7c2bc 80%,#9b8f86)" role="img" aria-label="Photo of young people sorting plastic bottles into a recycling tub"></div>
</section>

<section class="standout">
  <div class="photo" style="left:133px;top:2846px;width:473px;height:446px;background:linear-gradient(170deg,#5a5f55,#7b7d70 40%,#d9742f 55%,#4e5a58 80%)" role="img" aria-label="Photo of a worker in an orange hard hat facing a pile of sorted waste"></div>
  <h2 class="h-left" style="left:656px;top:2843px">WHAT MAKES US<br>STAND OUT?</h2>
  <div class="lime-rule" style="left:660px;top:2965px;width:62px"></div>
  <div class="copy" style="left:660px;top:3010px;width:408px;font-size:13.5px">Sed ut perspiciatis unde omnis iste natus error sit volu ptatem accusantium doloremque laudantium, totam rem aperiam, eaque ipsa quae ab illo inventore veritatis et quasi architecto beatae vitae dicta sunt explicabo.</div>
  <div class="stat" style="left:660px;top:3128px"><i class="stat-icon"></i><div><b>100+</b><span>years in waste<br>management</span></div></div>
  <div class="stat" style="left:868px;top:3128px"><i class="stat-icon"></i><div><b>130kt</b><span>plastic recycled</span></div></div>
  <div class="stat" style="left:660px;top:3233px"><i class="stat-icon"></i><div><b>34.5kt</b><span>surplus redistributed</span></div></div>
  <div class="stat" style="left:868px;top:3233px"><i class="stat-icon"></i><div><b>42,122</b><span>MT of waste managed</span></div></div>
</section>

<section class="quote">
  <div class="truck" role="img" aria-label="Photo of a smiling worker in high-visibility gear riding on a green refuse truck"></div>
  <h2>GET A FREE QUOTE</h2>
  <div class="rule"></div>
  <p>Get a free quote and organise your households waste collection. Submit the form with your details and we will get back to you.</p>
  <a class="btn">Get A Quote</a>
</section>

<section class="blog">
  <h2 class="h-left" style="left:128px;top:3898px">LATEST BLOG</h2>
  <div class="lime-rule" style="left:131px;top:3967px;width:62px"></div>
  <article class="post" style="left:131px;top:4018px">
    <div class="thumb" role="img" aria-label="Photo of a woman with eyes closed in warm sunset light" style="background:linear-gradient(135deg,#e8b27a,#b9735a 50%,#5d4a44)"></div>
    <time>07 June, 2024</time><h3>Lorem ipsum dolor sit amet consectetur</h3>
    <p>Sed ut perspiciatis unde omnis iste natus error sit volu ptatem accusantium doloremque laudantium, totam.</p>
  </article>
  <article class="post" style="left:458px;top:4018px">
    <div class="thumb" role="img" aria-label="Photo of a smiling woman in front of misty mountains" style="background:linear-gradient(160deg,#c5c9ce,#8c95a0 50%,#d8cfc3)"></div>
    <time>07 June, 2024</time><h3>Lorem ipsum dolor sit amet consectetur</h3>
    <p>Sed ut perspiciatis unde omnis iste natus error sit volu ptatem accusantium doloremque laudantium, totam.</p>
  </article>
  <article class="post" style="left:780px;top:4018px">
    <div class="thumb" role="img" aria-label="Photo of a blue grab crane over a scrap metal pile" style="background:linear-gradient(180deg,#bcd2e6,#9fb6cc 40%,#6f5c4d 65%,#3f3731)"></div>
    <time>07 June, 2024</time><h3>Lorem ipsum dolor sit amet consectetur</h3>
    <p>Sed ut perspiciatis unde omnis iste natus error sit volu ptatem accusantium doloremque laudantium, totam.</p>
  </article>
</section>

<footer class="site-footer">
  <div class="footer-rule"></div>
  <div class="brand" style="left:131px;top:4509px">
    <div class="brand-dot"></div>
    <div class="brand-name">Laanemetsa<br>Haldusgrupp</div>
  </div>
  <div class="abs" style="left:215px;top:4598px;font-size:15px">Follow us</div>
  <div class="socials" aria-label="Social media links"><i></i><i></i><i></i><i></i></div>

  <div class="footer-col" style="left:540px"><h4>Our Company</h4><ul><li>About</li><li>Services</li><li>News</li><li>Contact</li></ul></div>
  <div class="footer-col" style="left:722px"><h4>SERVICES</h4><ul><li>General Waste</li><li>Recycling</li><li>Food Waste</li><li>Glass Waste</li><li>Coffee Cup Recycling</li><li>Confidential Waste</li></ul></div>
  <div class="footer-col" style="left:913px"><h4>CONTACT US</h4>
    <div style="display:flex;gap:12px;align-items:center">
      <svg width="20" height="20" viewBox="0 0 24 24"><path d="M6.6 10.8a15 15 0 006.6 6.6l2.2-2.2a1 1 0 011-.25 11.4 11.4 0 003.6.6 1 1 0 011 1V20a1 1 0 01-1 1A17 17 0 013 4a1 1 0 011-1h3.5a1 1 0 011 1c0 1.25.2 2.45.6 3.6a1 1 0 01-.25 1z" fill="none" stroke="#222" stroke-width="1.5"/></svg>
      <div style="font-size:13px;line-height:18px;color:var(--text)"><span style="font-size:12px">Call Us</span><br><span style="font-size:15px;color:var(--ink)">+1 888 888 8888</span></div>
    </div>
  </div>
  <div class="abs" style="left:131px;top:4731px;width:938px;height:1px;background:var(--line)"></div>
  <p class="copyright">Copyright © 2024 All Rights Reserved</p>
</footer>

</body>
</html>
```